Bright Step Path Flyer, eyecatching

Hi,
To give you an idea of the business for design purposes, #BrighttStepPath is predominantly a recruitment and people development business, ran by me dedicated to training & assisting others in achieving extra income (pt or f/t) around their current commitments, people also have the opportunity to build their own business brand with my support. My brand colours are Red, White and Black, and I would like to incorporate the following text;

#BrightStepPath

Recruiting now! Start today & start earning!

Would you like an extra income, for…
A holiday?…A new car?…Lifestyle changes?
(Can you put a tick box or something similar adjacent to each)

Are you facing…
Redundancy? Birth of a new child? Hefty bills?

If so, I have the solution.

Contact Yvonne Darcott today: (can you insert the appropriate icon for each of the contact details)
Tel: 07700 900417
Chirpline: @Bright_StepPath
Email: Yvonne@brightsteppath-example.co.uk
Pagebook: www.pagebook-example.com/yvonbrightsteppath

Target Market(s)

Women aged 25-45 years, possibly busy mums too, wanting to earn additinal income to allow them more choices, be it family time, money, new challenge, meeting new people, personal development

Industry/Entity Type

Health And Wellness

Font styles to use
Serif
Sans Serif
Decorative
Script

Colors
ec1f27
ffffff
000000

Requirements
Must have
• My heels logo, be clear concise and eye catching, I also have the following strap line if you wish to use;
• Empowering other to achieve
• Also I have attached a closeup picture of myself but would ideally only like half my face to appear (leftside) similar to the other picture posted - if you can
Nice to have
• Perhaps adding other forms of graphics, or the 3rd picture I have attached with myself...possibly just the shoes though
Should not have
• Too many colours

```html
<!DOCTYPE html>
<html lang="en">
<head>
<meta charset="utf-8">
<title>Bright Step Path – Recruiting Now</title>
<link rel="stylesheet" href="https://fonts.googleapis.com/css2?family=Cinzel:wght@400;600;700;900&display=swap">
<style>
  :root {
    --red: #ec1f27;
    --red-soft: #f4595e;
    --black: #000000;
    --ink: #111111;
    --white: #ffffff;
    --fold-light: #ffffff;
    --fold-mid: #e4e4e4;
    --fold-dark: #b9b9b9;
    --tick: #4cc43a;
  }
  html, body {
    margin: 0;
    padding: 0;
    width: 1200px;
    height: 850px;
    overflow: hidden;
    background: var(--white);
  }
  .flyer {
    position: relative;
    width: 1200px;
    height: 850px;
    overflow: hidden;
    background: var(--white);
    font-family: "Cinzel", serif;
    color: var(--white);
  }
  .flyer__shapes {
    position: absolute;
    inset: 0;
  }
  .text {
    position: absolute;
    margin: 0;
    white-space: nowrap;
    text-transform: uppercase;
    letter-spacing: 0.06em;
    line-height: 1;
  }
  .brand-title {
    left: 522px;
    top: 48px;
    font-size: 45px;
    font-weight: 900;
    line-height: 48px;
    letter-spacing: 0.03em;
    color: var(--ink);
  }
  .tagline {
    left: 876px;
    top: 116px;
    font-size: 11px;
    font-weight: 600;
    letter-spacing: 0.08em;
    transform: rotate(-3deg);
    transform-origin: left bottom;
  }
  .recruiting {
    left: 812px;
    top: 128px;
    font-size: 19px;
    font-weight: 700;
    letter-spacing: 0.1em;
  }
  .question {
    font-size: 20px;
    font-weight: 700;
    line-height: 25px;
    letter-spacing: 0.13em;
  }
  .question--income { left: 744px; top: 212px; text-indent: 18px; }
  .question--facing { left: 744px; top: 406px; }
  .check-list {
    position: absolute;
    margin: 0;
    padding: 0;
    list-style: none;
    font-size: 15px;
    font-weight: 700;
    letter-spacing: 0.13em;
    text-transform: uppercase;
  }
  .check-list li {
    height: 19px;
    line-height: 19px;
    white-space: nowrap;
  }
  .check-list--income { left: 806px; top: 299px; }
  .check-list--facing { left: 766px; top: 450px; }
  .tick-box {
    position: absolute;
    width: 17px;
    height: 17px;
  }
  .solution {
    left: 890px;
    top: 612px;
    font-size: 20px;
    font-weight: 700;
    line-height: 24px;
    letter-spacing: 0.1em;
  }
  .contact-heading {
    left: 756px;
    top: 760px;
    font-size: 10.5px;
    font-weight: 700;
    letter-spacing: 0.08em;
    color: var(--ink);
  }
  .contact-list {
    position: absolute;
    left: 656px;
    top: 783px;
    margin: 0;
    padding: 0;
    list-style: none;
    font-size: 10.5px;
    font-weight: 700;
    line-height: 12px;
    letter-spacing: 0.04em;
    text-transform: uppercase;
    color: var(--ink);
  }
  .contact-list li { white-space: nowrap; }
</style>
</head>
<body>
<main class="flyer">
  <svg class="flyer__shapes" width="1200" height="850" viewBox="0 0 1200 850" xmlns="http://www.w3.org/2000/svg">
    <defs>
      <linearGradient id="fold-left" x1="0" x2="1" y1="0" y2="0">
        <stop offset="0" stop-color="var(--fold-dark)"/>
        <stop offset="0.35" stop-color="var(--fold-light)"/>
        <stop offset="1" stop-color="var(--fold-mid)"/>
      </linearGradient>
      <linearGradient id="fold-right" x1="0" x2="1" y1="0" y2="0">
        <stop offset="0" stop-color="var(--fold-mid)"/>
        <stop offset="0.5" stop-color="var(--fold-light)"/>
        <stop offset="1" stop-color="var(--fold-light)"/>
      </linearGradient>
      <linearGradient id="fold-narrow" x1="0" x2="1" y1="0" y2="0">
        <stop offset="0" stop-color="var(--fold-light)"/>
        <stop offset="1" stop-color="var(--fold-dark)"/>
      </linearGradient>
      <linearGradient id="portrait-tones" x1="0" x2="0" y1="0" y2="1">
        <stop offset="0" stop-color="#d9a6c4"/>
        <stop offset="0.45" stop-color="#e98fc3"/>
        <stop offset="0.75" stop-color="#a77b93"/>
        <stop offset="1" stop-color="#3f3a48"/>
      </linearGradient>
      <linearGradient id="shoe-tones" x1="0" x2="1" y1="0" y2="1">
        <stop offset="0" stop-color="#f5f5f5"/>
        <stop offset="0.4" stop-color="#e8545a"/>
        <stop offset="1" stop-color="#f3f3f3"/>
      </linearGradient>
    </defs>

    <polygon class="panel panel--left" points="0,0 140,0 140,850 70,850 40,790 0,850" fill="url(#fold-left)"/>
    <polygon class="panel panel--narrow" points="440,0 468,0 468,850 440,850" fill="url(#fold-narrow)"/>
    <rect class="panel panel--spine" x="468" y="0" width="48" height="850" fill="var(--black)"/>
    <polygon class="panel panel--right" points="516,0 652,0 652,850 600,850 560,790 516,850" fill="url(#fold-right)"/>

    <g role="img" aria-label="Close-up portrait photo of the business owner, left half of her face, in a dotted pink and blue screen effect">
      <polygon points="140,0 440,0 440,850 380,850 340,790 300,850 140,850" fill="url(#portrait-tones)"/>
    </g>

    <g role="img" aria-label="Photo of a red strappy high-heeled sandal with sparkling straps">
      <rect x="516" y="190" width="460" height="550" fill="url(#shoe-tones)"/>
    </g>

    <polygon class="wedge wedge--soft" points="1072,512 1200,448 1200,470" fill="var(--red-soft)"/>
    <polygon class="wedge wedge--red" points="1200,456 796,560 932,732 1200,820" fill="var(--red)"/>

    <polygon class="block block--black" points="792,0 1156,0 1200,44 1200,448 552,568" fill="var(--black)"/>

    <line x1="732" y1="150" x2="1200" y2="137" stroke="var(--white)" stroke-width="1.2"/>
  </svg>

  <h1 class="text brand-title">Bright<br>Step<br>Path</h1>

  <p class="text tagline">Start today &amp; start earning!</p>
  <p class="text recruiting">Recruiting now</p>

  <p class="text question question--income">Would you like an extra<br>income, for…</p>
  <ul class="check-list check-list--income">
    <li>A holiday?…</li>
    <li>A new car?…</li>
    <li>Lifestyle changes?</li>
  </ul>

  <p class="text question question--facing">Are you facing…</p>
  <ul class="check-list check-list--facing">
    <li>Redundancy?</li>
    <li>Birth of a new child?</li>
    <li>Hefty bills?</li>
  </ul>

  <svg class="tick-box" style="left:1044px;top:299px" viewBox="0 0 17 17"><rect x="0.5" y="0.5" width="16" height="16" fill="var(--white)"/><path d="M3 9 L7 13 L15 3" stroke="var(--tick)" stroke-width="3" fill="none"/></svg>
  <svg class="tick-box" style="left:1044px;top:318px" viewBox="0 0 17 17"><rect x="0.5" y="0.5" width="16" height="16" fill="var(--white)"/><path d="M3 9 L7 13 L15 3" stroke="var(--tick)" stroke-width="3" fill="none"/></svg>
  <svg class="tick-box" style="left:1044px;top:337px" viewBox="0 0 17 17"><rect x="0.5" y="0.5" width="16" height="16" fill="var(--white)"/><path d="M3 9 L7 13 L15 3" stroke="var(--tick)" stroke-width="3" fill="none"/></svg>
  <svg class="tick-box" style="left:1032px;top:451px" viewBox="0 0 17 17"><rect x="0.5" y="0.5" width="16" height="16" fill="var(--white)"/><path d="M3 9 L7 13 L15 3" stroke="var(--tick)" stroke-width="3" fill="none"/></svg>
  <svg class="tick-box" style="left:1032px;top:470px" viewBox="0 0 17 17"><rect x="0.5" y="0.5" width="16" height="16" fill="var(--white)"/><path d="M3 9 L7 13 L15 3" stroke="var(--tick)" stroke-width="3" fill="none"/></svg>
  <svg class="tick-box" style="left:1032px;top:489px" viewBox="0 0 17 17"><rect x="0.5" y="0.5" width="16" height="16" fill="var(--white)"/><path d="M3 9 L7 13 L15 3" stroke="var(--tick)" stroke-width="3" fill="none"/></svg>

  <p class="text solution">If so,<br>I have the solution.</p>

  <p class="text contact-heading">Contact Yvonne Darcott today:</p>
  <ul class="contact-list">
    <li>Tel: 07700 900417</li>
    <li>Chirpline: @Bright_StepPath</li>
    <li>Email: Yvonne@brightsteppath-example.co.uk</li>
    <li>Pagebook: www.pagebook-example.com/yvonbrightsteppath</li>
  </ul>
</main>
</body>
</html>
```